Business Card for my New Brokerage

Looking to get a business card design for my new Real Estate Brokerage.
I want it with Picture, Phone Number, Email, Website, Office Address
Name and Designation. Please add logo too.

Target Market(s)

Real Estate Investors or Home Buyers

Industry/Entity Type

Real Estate

Contact Information for Business Card

Name, Email, Phone Number, website, email, office address

Colors
EB3D1F
EC4F4E
F09395
F8D3D4
FCEDEE

Requirements
Must have
• Minimalistic, Clean, Modern, Photo
Nice to have
• White and Red Colors

```html
<!DOCTYPE html>
<html lang="en">
<head>
<meta charset="utf-8">
<title>Ember Realty Inc – Business Card</title>
<link rel="stylesheet" href="https://fonts.googleapis.com/css2?family=Montserrat:wght@400;600;700&display=swap">
<style>
  :root {
    --page-bg: #e8e8ec;
    --card-white: #ededf0;
    --brand-red: #cd1c23;
    --text-grey: #6b6b70;
    --navy: #1f2a44;
    --gold-start: #b8913a;
    --gold-end: #efd98c;
    --photo-top: #e4e5ea;
    --photo-bottom: #2a3350;
  }
  * { box-sizing: border-box; margin: 0; padding: 0; }
  html, body {
    width: 1200px; height: 1200px; overflow: hidden;
    background: var(--page-bg);
    font-family: "Montserrat", sans-serif;
  }
  .card {
    position: absolute; left: 227px; width: 746px; height: 425px; overflow: hidden;
  }
  .card--front { top: 135px; background: var(--card-white); }
  .card--back { top: 639px; background: var(--brand-red); }

  .brand { position: absolute; text-align: center; }
  .brand__name { display: block; font-weight: 700; line-height: 1; letter-spacing: 1px; }
  .brand__tag { display: block; font-weight: 400; line-height: 1; }

  .card--front .brand { left: 34px; top: 50px; color: var(--brand-red); }
  .card--front .brand__name { font-size: 84px; }
  .card--front .brand__tag { font-size: 24px; letter-spacing: 6px; margin-top: 10px; }

  .card--back .brand { left: 0; right: 0; top: 160px; color: #f3f3f5; }
  .card--back .brand__name { font-size: 128px; }
  .card--back .brand__tag { font-size: 34px; letter-spacing: 8px; margin-top: 14px; }

  .agent { position: absolute; left: 34px; top: 183px; }
  .agent__name { font-size: 25px; font-weight: 700; color: var(--brand-red); letter-spacing: 0.5px; }
  .agent__title { font-size: 19px; color: var(--text-grey); margin-top: 6px; }

  .contact { position: absolute; left: 34px; top: 262px; list-style: none; }
  .contact__item {
    display: flex; align-items: center; gap: 9px;
    font-size: 19px; color: var(--text-grey); height: 27px;
  }
  .contact__icon { width: 19px; height: 19px; flex: none; }

  .agent-photo {
    position: absolute; left: 474px; top: 25px; width: 272px; height: 331px;
    background: linear-gradient(180deg, var(--photo-top) 0%, var(--photo-top) 30%, var(--photo-bottom) 75%);
  }

  .address-band {
    position: absolute; left: 0; top: 356px; width: 746px; height: 44px;
    background: var(--brand-red);
  }
  .address-band__text {
    position: absolute; left: 34px; top: 11px;
    font-size: 19px; color: #f6f6f8;
  }
  .address-band__mark {
    position: absolute; left: 622px; top: 8px; width: 28px; height: 28px; background: var(--navy);
  }
  .address-band__gold {
    position: absolute; left: 655px; top: 0; width: 91px; height: 44px;
    background: linear-gradient(90deg, var(--gold-start), var(--gold-end));
  }
</style>
</head>
<body>
  <section class="card card--front">
    <div class="brand">
      <span class="brand__name">EMBER</span>
      <span class="brand__tag">REALTY INC</span>
    </div>

    <div class="agent">
      <h1 class="agent__name">DANIEL WHITFORD</h1>
      <p class="agent__title">Managing Director</p>
    </div>

    <ul class="contact">
      <li class="contact__item">
        <svg class="contact__icon" viewBox="0 0 20 20"><circle cx="10" cy="10" r="10" fill="#cd1c23"/><path d="M5 8c0-2 2-3 5-3s5 1 5 3l-2 1-1-1H8L7 9z M7 10h6l1 4H6z" fill="#fff"/></svg>
        <span>603 555 0148</span>
      </li>
      <li class="contact__item">
        <svg class="contact__icon" viewBox="0 0 20 20"><circle cx="10" cy="10" r="10" fill="#cd1c23"/><rect x="5" y="6.5" width="10" height="7" fill="none" stroke="#fff" stroke-width="1.3"/><path d="M5 6.5l5 4 5-4" fill="none" stroke="#fff" stroke-width="1.3"/></svg>
        <span>hello@emberrealty.com</span>
      </li>
      <li class="contact__item">
        <svg class="contact__icon" viewBox="0 0 20 20"><circle cx="10" cy="10" r="10" fill="#cd1c23"/><circle cx="10" cy="10" r="5.5" fill="none" stroke="#fff" stroke-width="1.2"/><path d="M4.5 10h11M10 4.5c-2 2-2 9 0 11M10 4.5c2 2 2 9 0 11" fill="none" stroke="#fff" stroke-width="1"/></svg>
        <span>www.emberrealty.com</span>
      </li>
    </ul>

    <div class="agent-photo" role="img" aria-label="Portrait photo of the agent in a navy suit with arms crossed"></div>

    <div class="address-band">
      <p class="address-band__text">415 Maple Avenue, Ste 2, Dover, NH 03820</p>
      <span class="address-band__mark"></span>
      <span class="address-band__gold"></span>
    </div>
  </section>

  <section class="card card--back">
    <div class="brand">
      <span class="brand__name">EMBER</span>
      <span class="brand__tag">REALTY INC</span>
    </div>
  </section>
</body>
</html>
```